Business Report Cover

We need a revamped quarterly report cover to send to our clients. We asset manage commercial and residential properties throughout the the United States. We use a .pdf version of a cover that we've used for years but would like a fresh updated look for 2018. The cover should include our company logo (KOV Enterprises) and a photo of the property as well as the Quarter/Year of the report.

```html
<!DOCTYPE html>
<html lang="en">
<head>
<meta charset="utf-8">
<title>KOV Enterprises – Quarterly Operating Report Q1 2018</title>
<link href="https://fonts.googleapis.com/css2?family=Kanit:wght@300;500;700&display=swap" rel="stylesheet">
<style>
  :root {
    --backdrop: #e9e7e3;
    --paper: #ffffff;
    --ink: #111111;
    --green: #4f9b6e;
    --green-soft: #3f9a63;
    --charcoal: #3a3a3a;
    --photo-light: #d9dcdf;
    --photo-mid: #8a8580;
    --photo-dark: #3b3638;
  }
  * { margin: 0; padding: 0; box-sizing: border-box; }
  html, body {
    width: 1200px; height: 1200px; overflow: hidden;
    background: var(--backdrop);
    font-family: "Kanit", sans-serif;
    color: var(--ink);
  }
  .cover {
    position: absolute; left: 200px; top: 36px;
    width: 800px; height: 1128px;
    background: var(--paper);
    overflow: hidden;
    box-shadow: 0 4px 14px rgba(0,0,0,.12);
  }
  .cover-art { position: absolute; inset: 0; width: 100%; height: 100%; }
  .brand {
    position: absolute; left: 46px; top: 48px;
    font-weight: 700; color: var(--ink); line-height: 1;
  }
  .brand-name { font-size: 76px; letter-spacing: -1px; }
  .brand-tag { font-size: 16px; letter-spacing: 7px; margin-top: 4px; }
  .title-rule {
    position: absolute; left: 62px; top: 855px;
    width: 317px; height: 7px; background: var(--ink);
  }
  .report-title {
    position: absolute; left: 62px; top: 872px;
    font-weight: 300; font-size: 23px; line-height: 32px;
    text-transform: uppercase; letter-spacing: -0.3px;
  }
  .report-year {
    position: absolute; left: 60px; top: 942px;
    font-weight: 500; font-size: 78px; line-height: 1; letter-spacing: -2px;
  }
  .property-address {
    position: absolute; left: 552px; top: 1024px;
    font-weight: 300; font-size: 17px; line-height: 24px;
    font-style: normal;
  }
</style>
</head>
<body>
  <main class="cover">
    <svg class="cover-art" viewBox="0 0 975 1375" preserveAspectRatio="none" aria-hidden="false">
      <defs>
        <linearGradient id="photoTone" x1="0" y1="0" x2="0" y2="1">
          <stop offset="0" stop-color="var(--photo-light)"/>
          <stop offset="0.35" stop-color="#c9cacd"/>
          <stop offset="0.5" stop-color="var(--photo-mid)"/>
          <stop offset="0.75" stop-color="#5e4a48"/>
          <stop offset="1" stop-color="var(--photo-dark)"/>
        </linearGradient>
      </defs>
      <path class="property-photo" role="img" aria-label="Photo of the managed property: a fuel station canopy with pumps in front of a brick building"
            d="M0 0 H975 V430 C 820 700, 560 900, 0 963 Z" fill="url(#photoTone)"/>
      <circle class="accent-circle-top" cx="898" cy="108" r="145" fill="var(--green-soft)" opacity="0.88"/>
      <circle class="accent-circle-dark" cx="843" cy="318" r="135" fill="var(--charcoal)" opacity="0.88"/>
      <circle class="accent-circle-bottom" cx="968" cy="1043" r="215" fill="var(--green)"/>
    </svg>

    <div class="brand">
      <div class="brand-name">KOV</div>
      <div class="brand-tag">ENTERPRISES</div>
    </div>

    <div class="title-rule"></div>
    <h1 class="report-title">Quarterly Operating Report<br>1st Quarter</h1>
    <div class="report-year">2018</div>

    <address class="property-address">
      Vancouver Corner Market<br>
      4120 NE Harbor Point Dr.<br>
      Vancouver, WA 98660
    </address>
  </main>
</body>
</html>
```